New Electrical Business Card Design

I would like a new design for my business cards.
i would like the same logo and font but new design
Please see attached files for front and back design.
large image can be used for graphics.
I would like the instagram link incorporated to back of card.
website site address needs to be changed to www.kestrelhillelectrical.au
everything else stays as is

```html
<!DOCTYPE html>
<html lang="en">
<head>
<meta charset="utf-8">
<title>Kestrel Hill Electrical &amp; Data – Business Card</title>
<link href="https://fonts.googleapis.com/css2?family=Montserrat:wght@400;700;800&display=swap" rel="stylesheet">
<style>
  :root {
    --bg: #e4e4e4;
    --card-dark: #2b2b2b;
    --card-light: #ffffff;
    --ink: #1c1c1c;
    --ink-soft: #333333;
    --green: #0f8a3c;
    --white: #ffffff;
  }
  * { box-sizing: border-box; margin: 0; padding: 0; }
  html, body { width: 1200px; height: 900px; overflow: hidden; }
  body {
    background: var(--bg);
    font-family: "Montserrat", sans-serif;
    display: flex;
    flex-direction: column;
    align-items: center;
    justify-content: center;
    gap: 36px;
  }
  .card {
    width: 660px;
    height: 400px;
    border-radius: 26px;
    position: relative;
    overflow: hidden;
    box-shadow: 0 6px 18px rgba(0,0,0,.18);
  }

  /* Wordmark */
  .wordmark {
    display: flex;
    align-items: center;
    gap: 12px;
    font-weight: 800;
    font-size: 26px;
    text-transform: uppercase;
    line-height: 1;
    white-space: nowrap;
  }
  .wordmark-dot {
    width: 20px; height: 20px; border-radius: 50%;
    background: var(--green);
    flex: none;
  }

  /* Back */
  .card-back {
    background: var(--card-dark);
    color: var(--white);
    display: flex;
    flex-direction: column;
    align-items: center;
    justify-content: center;
    gap: 44px;
    padding: 0 48px;
  }
  .card-back .wordmark { color: var(--white); }
  .instagram {
    display: flex; align-items: center; gap: 10px;
    font-size: 20px; letter-spacing: .5px; font-weight: 400;
  }
  .instagram-dot {
    width: 14px; height: 14px; border-radius: 50%;
    border: 2px solid var(--green);
  }

  /* Front */
  .card-front { background: var(--card-light); color: var(--ink); }
  .accent-bar {
    position: absolute; top: 32px; right: 0;
    width: 34px; height: 66px; background: var(--green);
  }
  .holder {
    position: absolute; top: 34px; right: 52px;
    text-align: right;
  }
  .holder-name {
    color: var(--green); font-weight: 800; font-size: 22px;
    letter-spacing: .8px; text-transform: uppercase;
  }
  .holder-meta { font-size: 15px; color: var(--ink-soft); margin-top: 4px; line-height: 1.35; }
  .card-front .wordmark {
    position: absolute; left: 46px; top: 150px;
    color: var(--ink);
  }
  .contact {
    position: absolute; left: 46px; bottom: 34px;
    font-size: 16px; color: var(--ink-soft);
  }
  .contact-row { display: flex; align-items: center; gap: 10px; line-height: 1.55; }
  .contact-row svg { width: 16px; height: 16px; flex: none; }
  .services {
    margin-top: 8px;
    font-weight: 700; font-size: 17px; color: var(--ink);
    display: grid; grid-template-columns: auto auto; column-gap: 12px; row-gap: 2px;
  }
  .services span::before { content: "• "; color: var(--green); }
</style>
</head>
<body>

<section class="card card-back" aria-label="Card back">
  <div class="wordmark"><span class="wordmark-dot"></span>Kestrel Hill Electrical &amp; Data</div>
  <div class="instagram"><span class="instagram-dot"></span>kestrel.hill.electrical</div>
</section>

<section class="card card-front" aria-label="Card front">
  <div class="accent-bar"></div>
  <div class="holder">
    <div class="holder-name">Daniel Ostrowski</div>
    <div class="holder-meta">ABN - 62 118 407 935<br>Lic Number - 418603D</div>
  </div>

  <div class="wordmark"><span class="wordmark-dot"></span>Kestrel Hill Electrical &amp; Data</div>

  <div class="contact">
    <div class="contact-row">
      <svg viewBox="0 0 16 16"><path fill="var(--green)" d="M3.5 1.5l2.5 0 1 3.5-1.6 1.2a8 8 0 0 0 4.4 4.4L11 9l3.5 1v2.5c0 1-.8 1.8-1.8 1.7C7 13.7 2.3 9 1.8 3.3 1.7 2.3 2.5 1.5 3.5 1.5z"/></svg>
      0412 558 903
    </div>
    <div class="contact-row">
      <svg viewBox="0 0 16 16"><rect x="1" y="3" width="14" height="10" rx="1" fill="var(--green)"/><path d="M1.5 3.8L8 9l6.5-5.2" fill="none" stroke="#fff" stroke-width="1.3"/></svg>
      info@kestrelhillelectrical.au
    </div>
    <div class="contact-row">
      <svg viewBox="0 0 16 16"><circle cx="8" cy="8" r="6.5" fill="none" stroke="var(--green)" stroke-width="1.5"/><ellipse cx="8" cy="8" rx="2.8" ry="6.5" fill="none" stroke="var(--green)" stroke-width="1.2"/><path d="M1.5 8h13" stroke="var(--green)" stroke-width="1.2"/></svg>
      www.kestrelhillelectrical.au
    </div>
    <div class="services">
      <span>Residential</span><span>Commercial</span>
      <span>Industrial</span><span>24hr Service</span>
    </div>
  </div>
</section>

</body>
</html>
```